Ad for Cyber Security Company- Print Ad

We are looking for an awesome designer to create a one page advertisement for the Kelvora Security data analytics platform that will be featured in an upcoming security magazine. This is also going to be featured in an upcoming trade show. Kelvora Security produced the KELVORA platform to help companies unify their security environment and help them address Insider Threat, Fraud and Anomaly ID and resolution. KELVORA uses an an advanced ingestion engine, machine learning, and workflow automation to ensure the right people are getting the right info at the right time. We serve enterprise level customers, augmenting and enhancing, not replacing their existing security stack. We would like few or single image, clean, and open ad built around the tagline 'Make Security a Team Sport.' We would like the logo to be featured, and include our website address on the page (www.kelvorasecurity.net). See below for style guide.

Target Market(s)

Industry insiders, Chief Information Security Officers (CISO) and Technical directors.

Other font styles liked:
• See style guide, but we are open to suggestion.

Requirements
Must have
• A single image (minimum), Feature the provided logo, Include the tagline 'Make Security a Team Sport' and have the website somewhere on the ad. The image should focus on the conveying the message of "Make Security a Team Sport" and not be a generic security (padlock, network, etc.) image.
• See included style guide.

```html
<!DOCTYPE html>
<html lang="en">
<head>
<meta charset="utf-8">
<title>Kelvora Security – Make Security a Team Sport</title>
<link href="https://fonts.googleapis.com/css2?family=Fira+Sans:wght@600;700;800&family=Open+Sans:wght@400;600&display=swap" rel="stylesheet">
<style>
  :root {
    --orange: #f26522;
    --charcoal: #3b3b3d;
    --ink: #111417;
    --slate: #5a5b5e;
    --white: #ffffff;
    --text-dark: #2b2b2b;
    --backdrop: #d4d4d4;
  }
  * { box-sizing: border-box; margin: 0; padding: 0; }
  html, body { width: 1200px; height: 1200px; overflow: hidden; }
  body { background: var(--backdrop); font-family: "Open Sans", sans-serif; }

  .flyer {
    position: absolute; left: 157px; top: 30px;
    width: 886px; height: 1140px; overflow: hidden;
    background: var(--charcoal);
  }
  .flyer__art { position: absolute; inset: 0; width: 886px; height: 1140px; }

  .brand {
    position: absolute; left: 34px; top: 36px;
    display: flex; align-items: center; gap: 14px;
  }
  .brand__mark { width: 58px; height: 58px; background: var(--charcoal); }
  .brand__name {
    font-family: "Fira Sans", sans-serif; font-weight: 800;
    color: var(--orange); font-size: 32px; line-height: 30px;
    letter-spacing: 2px; text-transform: uppercase;
  }

  .tagline {
    position: absolute; left: 455px; top: 472px; width: 420px;
    font-family: "Fira Sans", sans-serif; font-weight: 700;
    color: var(--white); font-size: 53px; line-height: 62px;
    text-align: center;
  }

  .intro-panel {
    position: absolute; left: 35px; top: 688px; width: 352px;
    color: var(--white); text-align: justify;
  }
  .intro-panel__lead { font-size: 20.5px; line-height: 24px; margin-bottom: 18px; }
  .intro-panel p.intro-panel__body { font-size: 14.6px; line-height: 16.8px; margin-bottom: 16px; }

  .about-badge {
    position: absolute; left: 695px; top: 669px; width: 191px; height: 48px;
    background: var(--orange); border-radius: 24px 0 0 24px;
    font-family: "Fira Sans", sans-serif; font-weight: 700;
    color: var(--white); font-size: 26px; line-height: 48px; text-align: center;
  }
  .about-badge::after {
    content: ""; position: absolute; left: 40px; right: 0; bottom: -9px; height: 4px;
    background: #9a9a9a; border-radius: 4px 0 0 4px;
  }

  .about-copy {
    position: absolute; left: 433px; top: 738px; width: 422px;
    color: var(--text-dark); font-size: 14.6px; line-height: 16.8px; text-align: justify;
  }
  .about-copy p { margin-bottom: 14px; }

  .footer-tag {
    position: absolute; left: 33px; top: 1069px;
    display: flex; align-items: center; gap: 8px;
    font-family: "Fira Sans", sans-serif; font-weight: 700;
    color: var(--charcoal); font-size: 26px; letter-spacing: 0.5px;
  }
  .footer-tag__dot { width: 20px; height: 20px; border-radius: 50%; background: var(--orange); }

  .contact {
    position: absolute; left: 430px; top: 1054px; width: 456px; height: 86px;
    background: var(--orange); border-radius: 30px 0 0 0;
  }
  .contact__list { position: absolute; left: 24px; top: 9px; list-style: none; }
  .contact__item {
    display: flex; align-items: center; gap: 12px;
    color: var(--white); font-size: 19px; line-height: 25px;
  }
  .contact__icon { width: 15px; height: 15px; }
  .contact__social { position: absolute; left: 349px; top: 19px; display: flex; gap: 8px; }
  .contact__social span {
    width: 33px; height: 33px; border-radius: 50%; background: var(--white);
  }
</style>
</head>
<body>
<main class="flyer">
  <svg class="flyer__art" viewBox="0 0 886 1140" aria-hidden="false">
    <defs>
      <radialGradient id="circuitGlow" cx="215" cy="310" r="330" gradientUnits="userSpaceOnUse">
        <stop offset="0" stop-color="#1f9fb6"/>
        <stop offset="0.45" stop-color="#0f5867"/>
        <stop offset="1" stop-color="#0b1519"/>
      </radialGradient>
      <linearGradient id="polyGray" x1="0" y1="0" x2="1" y2="1">
        <stop offset="0" stop-color="#6a6b6e"/>
        <stop offset="1" stop-color="#3d3e41"/>
      </linearGradient>
      <linearGradient id="screenGray" x1="0" y1="0" x2="0" y2="1">
        <stop offset="0" stop-color="#2a2b2e"/>
        <stop offset="0.72" stop-color="#7d7f84"/>
        <stop offset="1" stop-color="#d9d9dc"/>
      </linearGradient>
      <clipPath id="belowCurve">
        <path d="M0,437 C120,600 300,675 420,672 C600,668 760,630 886,585 V1140 H0 Z"/>
      </clipPath>
    </defs>

    <!-- hero band -->
    <rect x="0" y="0" width="886" height="700" fill="var(--ink)"/>
    <rect role="img" aria-label="Glowing digital shield with keyhole surrounded by circuit rings" x="0" y="140" width="560" height="520" fill="url(#circuitGlow)"/>

    <!-- monitor disc -->
    <circle cx="717" cy="149" r="320" fill="var(--orange)"/>
    <circle cx="717" cy="149" r="311" fill="url(#polyGray)"/>
    <rect role="img" aria-label="Desktop monitor displaying the threat analytics dashboard" x="488" y="94" width="366" height="290" rx="6" fill="url(#screenGray)"/>

    <!-- top white cap -->
    <path d="M0,0 H556 C516,100 392,170 240,176 C150,180 60,176 0,172 Z" fill="var(--orange)"/>
    <path d="M0,0 H540 C500,90 380,152 240,158 C150,162 60,160 0,156 Z" fill="var(--white)"/>

    <!-- lower swoosh -->
    <path transform="translate(0,-24)" d="M0,437 C120,600 300,675 420,672 C600,668 760,630 886,585 V1140 H0 Z" fill="var(--slate)"/>
    <path transform="translate(0,-12)" d="M0,437 C120,600 300,675 420,672 C600,668 760,630 886,585 V1140 H0 Z" fill="var(--orange)"/>
    <g clip-path="url(#belowCurve)">
      <rect x="0" y="400" width="886" height="740" fill="var(--white)"/>
      <path d="M0,400 H409 V961 Q409,1001 369,1001 H0 Z" fill="var(--charcoal)"/>
    </g>

    <!-- footer band -->
    <rect x="0" y="1111" width="886" height="29" fill="var(--orange)"/>
  </svg>

  <div class="brand">
    <span class="brand__mark"></span>
    <span class="brand__name">Kelvora<br>Security</span>
  </div>

  <h1 class="tagline">Make Security<br>a Team Sport</h1>

  <section class="intro-panel">
    <p class="intro-panel__lead">KELVORA is a security data analytics platform, enabling security teams and business partners with timely, actionable alerts and intelligence.</p>
    <p class="intro-panel__body">KELVORA moves as fast as you. With a variety of deployment models including on-premises, hybrid, or fully cloud-based, clients measure ROI in weeks, not months.</p>
    <p class="intro-panel__body">KELVORA makes security a team sport. Leveraging advanced machine learning and workflow optimization, KELVORA ensures that the right information is making it to the right people every time.</p>
  </section>

  <h2 class="about-badge">About Us</h2>

  <section class="about-copy">
    <p>KELVORA security data analytics platform that will be featured in an upcoming security magazine. This is also going to be featured in an upcoming trade show.</p>
    <p>Kelvora Security produced the KELVORA platform to help companies unify their security environment and help them address Insider Threat, Fraud and Anomaly ID and resolution.</p>
    <p>KELVORA uses an an advanced ingestion engine, machine learning, and workflow automation to ensure the right people are getting the right info at the right time. We serve enterprise level customers, augmenting and enhancing, not replacing their existing security stack.</p>
    <p>KELVORA complements existing tools, including SIEM and UBA, to provide enhanced visibility into your organization’s blind spots.</p>
  </section>

  <div class="footer-tag"><span class="footer-tag__dot"></span>IPSUM QUIA DOLOR</div>

  <footer class="contact">
    <ul class="contact__list">
      <li class="contact__item">
        <svg class="contact__icon" viewBox="0 0 16 16"><circle cx="8" cy="8" r="6.5" fill="none" stroke="#fff" stroke-width="2"/><rect x="5" y="6" width="6" height="4" fill="#fff"/></svg>
        ipsumquiadolorsitamet
      </li>
      <li class="contact__item">
        <svg class="contact__icon" viewBox="0 0 16 16"><circle cx="8" cy="8" r="6.5" fill="none" stroke="#fff" stroke-width="1.5"/><ellipse cx="8" cy="8" rx="3" ry="6.5" fill="none" stroke="#fff" stroke-width="1.2"/><line x1="1.5" y1="8" x2="14.5" y2="8" stroke="#fff" stroke-width="1.2"/></svg>
        www.kelvorasecurity.net
      </li>
    </ul>
    <div class="contact__social"><span></span><span></span></div>
  </footer>
</main>
</body>
</html>
```